New Web Design Project

Number of Pages Required

1 page

Requirements
Must have
• An Overview / Background of the Business & Services(not for profit rescue animal farm)
• The Target Market / Audience you are trying to reach (animal lovers)
• Design Specifics; any preferences or ideas for Style, Colour, Imagery, etc (no preferences)

```html
<!DOCTYPE html>
<html lang="en">
<head>
<meta charset="utf-8">
<title>Cedar Hollow Farms</title>
<link rel="stylesheet" href="https://fonts.googleapis.com/css2?family=Montserrat:wght@400;500;600;700&family=Open+Sans:wght@400;600&display=swap">
<style>
:root{
  --orange:#eca517;
  --orange-dark:#c98a0c;
  --ink:#222222;
  --text:#555555;
  --white:#ffffff;
  --footer:#1d1d1d;
  --footer-text:#a9a9a9;
  --grass:#4f7a2c;
  --grass-dark:#22311a;
}
*{margin:0;padding:0;box-sizing:border-box}
html,body{width:1200px;height:3015px;overflow:hidden}
body{position:relative;background:var(--white);font-family:"Open Sans",Arial,sans-serif;color:var(--text)}
.abs{position:absolute}
.heading{font-family:"Montserrat",Arial,sans-serif}

/* hero */
.hero{left:0;top:0;width:1200px;height:615px;background:linear-gradient(180deg,#1c2414 0%,#2f4a1f 25%,var(--grass) 50%,#3d5d25 75%,var(--grass-dark) 100%)}
.hero-shade{left:0;top:0;width:1200px;height:615px;background:rgba(0,0,0,.28)}
.logo{left:142px;top:18px;font-family:"Montserrat",Arial,sans-serif;font-size:32px;font-weight:500;color:var(--orange)}
.nav{top:28px;font-family:"Montserrat",Arial,sans-serif;font-size:17px;color:var(--white)}
.nav.active{color:var(--orange)}
.hero-title{left:0;top:222px;width:1200px;text-align:center;font-family:"Montserrat",Arial,sans-serif;font-size:42px;line-height:50px;color:var(--white)}
.btn-solid{background:var(--orange);color:var(--ink);font-family:"Montserrat",Arial,sans-serif;text-align:center}
.hero-btn{left:535px;top:335px;width:128px;height:42px;line-height:42px;font-size:17px;border-radius:3px}
.slide-arrow{top:290px;width:30px;height:32px;background:rgba(0,0,0,.7)}

/* welcome */
.welcome-title{left:145px;top:696px;font-size:34px;font-weight:600;color:var(--orange)}
.welcome-text{left:145px;top:750px;width:605px;font-size:13.5px;line-height:25px}
.pill{border-radius:23px;font-size:13px;font-weight:600;height:45px;line-height:45px}
.welcome-btn{left:145px;top:895px;width:132px}
.welcome-photo{left:813px;top:693px;width:244px;height:244px;border-radius:50%;border:6px solid var(--orange);background:linear-gradient(135deg,#6f8fa0,#cfc8bb 55%,#8a7d68)}

/* services */
.services{left:0;top:1020px;width:1200px;height:530px;background:var(--orange)}
.services-title{left:0;top:1092px;width:1200px;text-align:center;font-size:34px;font-weight:600;color:var(--ink)}
.service-icon{top:1158px;width:130px;height:130px;background:var(--white);box-shadow:9px 9px 0 var(--orange-dark)}
.service-icon svg{position:absolute;left:25px;top:25px}
.service-name{top:1315px;width:300px;text-align:center;font-size:24px;font-weight:600;color:var(--ink)}
.service-text{top:1352px;width:300px;text-align:center;font-size:11px;line-height:17px;color:var(--ink)}
.outline-btn{top:1418px;width:132px;height:45px;line-height:41px;border:2px solid var(--ink);border-radius:23px;text-align:center;font-family:"Montserrat",Arial,sans-serif;font-size:13px;font-weight:600;color:var(--ink)}

/* gallery */
.section-title{left:0;width:1200px;text-align:center;font-size:34px;font-weight:600;color:var(--orange)}
.tile{background:#999}
.play{left:576px;top:1864px;width:48px;height:48px;border-radius:50%;background:var(--white);border:3px solid rgba(0,0,0,.25)}
.view-btn{left:534px;top:2105px;width:132px}

/* map + footer */
.footer{left:0;top:2614px;width:1200px;height:401px;background:var(--footer)}
.map{left:144px;top:2280px;width:911px;height:438px;background:linear-gradient(135deg,#e4e4e4,#d4d8d0 40%,#cfe3ea 55%,#dfe6d6)}
.foot-head{top:2770px;font-family:"Montserrat",Arial,sans-serif;font-size:18px;color:var(--white)}
.foot-line{font-size:12px;color:var(--footer-text)}
.social{top:2810px;width:28px;height:28px;border-radius:50%;background:#6b6b6b}
.divider{left:144px;top:2918px;width:911px;height:1px;background:#444}
.copyright{left:0;top:2958px;width:1200px;text-align:center;font-size:12px;color:var(--footer-text)}
</style>
</head>
<body>

<header>
  <div class="abs hero" role="img" aria-label="Photo of goats grazing on a green meadow behind a wooden fence"></div>
  <div class="abs hero-shade"></div>
  <div class="abs logo">Cedar Hollow Farms</div>
  <nav>
    <span class="abs nav active" style="left:560px">Home</span>
    <span class="abs nav" style="left:651px">About Us</span>
    <span class="abs nav" style="left:766px">Services</span>
    <span class="abs nav" style="left:871px">Gallery</span>
    <span class="abs nav" style="left:967px">Contact Us</span>
  </nav>
  <h1 class="abs hero-title" style="font-weight:400">Donec aliquam<br>eget euismod dictum</h1>
  <div class="abs btn-solid hero-btn">Read More</div>
  <div class="abs slide-arrow" style="left:0"><svg width="30" height="32"><path d="M18 10 L12 16 L18 22" stroke="#fff" stroke-width="2.5" fill="none"/></svg></div>
  <div class="abs slide-arrow" style="left:1170px"><svg width="30" height="32"><path d="M12 10 L18 16 L12 22" stroke="#fff" stroke-width="2.5" fill="none"/></svg></div>
</header>

<section class="welcome">
  <h2 class="abs heading welcome-title">Welcome to Cedar Hollow Farms</h2>
  <p class="abs welcome-text">Maecenas vel tortor accumsan quam varius imperdiet vel eget elit. Aenean facilisis tincidunt lectus, id dictum nisi luctus eget. Vivamus efficitur ex condimentum, malesuada eros eget, feugiat nibh. Sed tellus ex, imperdiet eget gravida sit amet, volutpat eget turpis. In nec ultricies est. Etiam mattis augue vehicula odio posuere, sit amet tempus lectus luctus. Nulla facilisi. Etiam vel massa elementum, bibendum tellus venenatis, feugiat massa. Curabitur venenatis lacinia ornare.</p>
  <div class="abs btn-solid pill welcome-btn">READ MORE</div>
  <div class="abs welcome-photo" role="img" aria-label="Photo of a lamb drinking from a feeding bottle"></div>
</section>

<section>
  <div class="abs services"></div>
  <h2 class="abs heading services-title">Services</h2>

  <div class="abs service-icon" style="left:220px">
    <svg width="80" height="80" viewBox="0 0 80 80" fill="none" stroke="#1e2f6e" stroke-width="3" stroke-linejoin="round">
      <rect x="28" y="24" width="24" height="46" rx="5"/><path d="M32 24 L34 14 H46 L48 24"/><path d="M37 14 V8 H43 V14"/><path d="M36 40 H44 M36 50 H44 M36 60 H44"/>
    </svg>
  </div>
  <div class="abs service-icon" style="left:531px">
    <svg width="80" height="80" viewBox="0 0 80 80" fill="none" stroke="#1e2f6e" stroke-width="3" stroke-linejoin="round">
      <rect x="10" y="36" width="60" height="14" rx="3"/><rect x="10" y="54" width="60" height="14" rx="3"/><rect x="16" y="22" width="16" height="14"/><rect x="34" y="16" width="14" height="20"/><rect x="50" y="24" width="14" height="12"/><circle cx="26" cy="43" r="2"/><circle cx="54" cy="61" r="2"/><circle cx="40" cy="43" r="2"/><circle cx="40" cy="61" r="2"/>
    </svg>
  </div>
  <div class="abs service-icon" style="left:842px">
    <svg width="80" height="80" viewBox="0 0 80 80" fill="none" stroke="#1e2f6e" stroke-width="3" stroke-linejoin="round">
      <path d="M40 68 L12 38 C2 26 10 10 24 12 C32 13 37 19 40 24 C43 19 48 13 56 12 C70 10 78 26 68 38 Z"/>
    </svg>
  </div>

  <h3 class="abs heading service-name" style="left:139px">MAECENAS VEL</h3>
  <h3 class="abs heading service-name" style="left:450px">CURABITUR</h3>
  <h3 class="abs heading service-name" style="left:761px">ETIAM MATTIS</h3>

  <p class="abs service-text" style="left:139px">Etiam mattis augue vehicula odio posuere, sit amet tempus lectus luctus. Nulla facilisi. Etiam vel massa elementum, bibendum tellus venenatis</p>
  <p class="abs service-text" style="left:450px">Etiam mattis augue vehicula odio posuere, sit amet tempus lectus luctus. Nulla facilisi. Etiam vel massa elementum, bibendum tellus venenatis</p>
  <p class="abs service-text" style="left:761px">Etiam mattis augue vehicula odio posuere, sit amet tempus lectus luctus. Nulla facilisi. Etiam vel massa elementum, bibendum tellus venenatis</p>

  <div class="abs outline-btn" style="left:223px">READ MORE</div>
  <div class="abs outline-btn" style="left:534px">READ MORE</div>
  <div class="abs outline-btn" style="left:845px">READ MORE</div>
</section>

<section>
  <h2 class="abs heading section-title" style="top:1630px">Gallery</h2>
  <div class="abs tile" style="left:144px;top:1693px;width:218px;height:187px;background:linear-gradient(135deg,#d9d9dc,#a9a9ad)" role="img" aria-label="Photo of a grey kitten"></div>
  <div class="abs tile" style="left:144px;top:1893px;width:218px;height:187px;background:linear-gradient(135deg,#c98a5a,#7a5a40)" role="img" aria-label="Photo of a guinea pig"></div>
  <div class="abs tile" style="left:374px;top:1693px;width:452px;height:387px;background:linear-gradient(135deg,#c8b894,#8c8576 50%,#5a5a55)" role="img" aria-label="Video still of a rabbit sitting by a window"></div>
  <div class="abs play"><svg width="42" height="42"><path d="M16 12 L30 21 L16 30 Z" fill="#333"/></svg></div>
  <div class="abs tile" style="left:838px;top:1693px;width:217px;height:187px;background:linear-gradient(135deg,#4e7a3a,#a69a7a 55%,#6d8a3a)" role="img" aria-label="Photo of gloved hands holding a small rescued animal"></div>
  <div class="abs tile" style="left:838px;top:1893px;width:217px;height:187px;background:linear-gradient(135deg,#4a6a2a,#6d6a5a 55%,#3a4a22)" role="img" aria-label="Photo of a raccoon on the forest floor"></div>
  <div class="abs btn-solid pill view-btn">VIEW ALL</div>
</section>

<section>
  <h2 class="abs heading section-title" style="top:2220px">Contact Us</h2>
  <div class="abs footer"></div>
  <div class="abs map" role="img" aria-label="Street map showing the farm location along a river"></div>
</section>

<footer>
  <h4 class="abs foot-head" style="left:144px;font-weight:400">Contact info</h4>
  <p class="abs foot-line" style="left:144px;top:2807px">24 Building name, Street name, City Zipcode</p>
  <p class="abs foot-line" style="left:144px;top:2831px">Ph : 555 014 2290</p>
  <p class="abs foot-line" style="left:144px;top:2855px">Em : info@cedarhollowfarms.org</p>

  <h4 class="abs foot-head" style="left:587px;font-weight:400">Links</h4>
  <p class="abs foot-line" style="left:587px;top:2807px">Home</p>
  <p class="abs foot-line" style="left:587px;top:2831px">About Us</p>
  <p class="abs foot-line" style="left:587px;top:2855px">Services</p>
  <p class="abs foot-line" style="left:676px;top:2807px">Gallery</p>
  <p class="abs foot-line" style="left:676px;top:2831px">Contact Us</p>

  <h4 class="abs foot-head" style="left:945px;font-weight:400">Follow us on</h4>
  <div class="abs social" style="left:946px" aria-label="Social profile one"></div>
  <div class="abs social" style="left:986px" aria-label="Social profile two"></div>
  <div class="abs social" style="left:1026px" aria-label="Social profile three"></div>

  <div class="abs divider"></div>
  <p class="abs copyright">Copyright &copy; 2019 &nbsp;Cedar Hollow Farms. &nbsp;&nbsp;All rights reserved.</p>
</footer>

</body>
</html>
```